CritterAsk.net Skin

I need a header image, backgroundand partial colour scheme for our website critterask.net.

We use a cms so have very limited ability to change the design.

We can change: link / button colour, header size and image, background image.
See these examples: http://replies.moonbrackle.example/ and http://aid.zorvat.example/

Target Market(s)

Pet owners are the audience, probably slightly more females than males.

Number of Pages Required

1 page

Requirements
Nice to have
• Should be friendly and fun with an "organic" feel. Can contain images of pets but it isn"t a requirement.

```html
<!DOCTYPE html>
<html lang="en">
<head>
<meta charset="utf-8">
<title>CritterAsk.net – Ask a Question</title>
<link href="https://fonts.googleapis.com/css2?family=Ubuntu:wght@400;500;700&family=Arimo:wght@400;700&display=swap" rel="stylesheet">
<style>
:root{
  --orange:#f39200;
  --ink:#1f1f1f;
  --muted:#7a7a7a;
  --rule:#e3e3e3;
  --panel:#ededed;
  --paper:#f6ecd6;
  --backdrop:#85786a;
  --white:#ffffff;
}
*{box-sizing:border-box;margin:0;padding:0}
html,body{width:1129px;height:1200px;overflow:hidden}
body{position:relative;font-family:"Arimo",Arial,sans-serif;color:var(--ink);background:var(--backdrop)}
a{color:inherit;text-decoration:none}
.abs{position:absolute}

.page{left:222px;top:25px;width:689px;height:1102px;background:var(--white);border-radius:6px;overflow:hidden}
.header{left:0;top:0;width:689px;height:205px;background:linear-gradient(180deg,#f8efdc,var(--paper))}
.header-art{left:430px;top:65px;width:210px;height:135px;border-radius:40px 40px 10px 10px;
  background:linear-gradient(90deg,#e9b3ad,#7b6f68 45%,#c2bdb3 65%,#b46f2e)}
.tape{background:rgba(230,170,70,.75)}
.logo{left:39px;top:20px;font-family:"Ubuntu",sans-serif;font-weight:700;font-size:37px;color:var(--orange);letter-spacing:-.5px}
.logo-dot{left:216px;top:32px;width:20px;height:20px;border-radius:50%;background:var(--orange)}
.tagline{left:48px;top:66px;font-family:"Ubuntu",sans-serif;font-size:14px;color:#2a2a2a}
.join{left:522px;top:18px;font-family:"Ubuntu",sans-serif;font-weight:500;font-size:13px;color:var(--orange)}
.join small{font-size:10px;margin:0 4px}
.btn-ask-top{left:573px;top:16px;width:108px;height:24px;background:var(--orange);color:var(--white);
  font-family:"Ubuntu",sans-serif;font-weight:500;font-size:12.5px;line-height:24px;text-align:center;border-radius:2px}
.nav{right:12px;top:188px;font-family:"Arimo",sans-serif;font-weight:700;font-size:9px;color:var(--orange)}
.nav a{margin-left:6px}

.h-ask{left:30px;top:212px;font-family:"Ubuntu",sans-serif;font-weight:500;font-size:18.5px}
.avatar{width:32px;height:32px;background:var(--orange);border-radius:2px;overflow:hidden}
.avatar svg{display:block}
.composer{left:64px;top:254px;width:394px;height:95px;border:1px solid #d6d6d6}
.tag-input{left:64px;top:359px;width:194px;height:23px;border:1px solid #d6d6d6;font-size:7.5px;color:#999;padding:7px 0 0 20px;font-weight:700}
.btn-ask{left:357px;top:359px;width:102px;height:25px;border:1px solid #cfcfcf;border-radius:3px;
  background:linear-gradient(#fff,#ececec);font-family:"Ubuntu",sans-serif;font-weight:500;font-size:12.5px;text-align:center;line-height:23px}
.dash{left:25px;width:656px;border-top:1px dashed #dcdcdc}

.h-latest{left:25px;top:407px;font-family:"Arimo",sans-serif;font-weight:700;font-size:18px}
.rss{left:180px;top:415px;width:9px;height:9px;background:var(--orange)}
.tabs{left:296px;top:414px;width:385px;height:20px;border-bottom:1px solid var(--rule)}
.tab{position:absolute;top:0;height:20px;font-family:"Arimo",sans-serif;font-weight:700;font-size:8.5px;line-height:20px;text-align:center;
  background:#e8e8e8;color:#666;border-radius:2px 2px 0 0}
.tab.active{background:var(--white);color:var(--orange);border:1px solid var(--rule);border-bottom-color:var(--white);height:21px}

.questions{left:25px;top:435px;width:434px;list-style:none}
.q{position:relative;border-bottom:1px dashed #dcdcdc;height:55px}
.q.two{height:70.5px}
.q.four{height:102px}
.q .avatar{position:absolute;left:0;top:8px}
.q .photo{background:linear-gradient(#9c8a73,#6b5a48)}
.count{position:absolute;left:3px;top:31px;width:37px;height:11px;background:var(--orange);border-radius:2px;color:var(--white);font-size:8px;font-weight:700;text-align:right;padding-right:4px;line-height:11px}
.count::before{content:"";position:absolute;left:6px;top:3px;width:7px;height:5px;background:#8a3e00;border-radius:1px}
.q h3{position:absolute;left:46px;top:6px;width:390px;font-family:"Arimo",sans-serif;font-weight:700;font-size:12.8px;line-height:16.2px}
.meta{position:absolute;left:46px;font-size:9px;color:var(--muted);bottom:10px}
.meta a{color:#333}
.tag{display:inline-block;border:1px solid #ddd;padding:1px 3px;font-size:7.5px;color:#999;margin-left:4px;font-weight:700}

.pager{left:25px;top:1075px;display:flex;border:1px solid #ddd;border-radius:2px}
.pager span{height:17px;min-width:17px;padding:0 5px;font-size:8px;font-weight:700;color:var(--orange);line-height:17px;border-right:1px solid #ddd;text-align:center}
.pager span:last-child{border-right:0}
.pager .current{background:var(--orange);color:var(--white)}

.sidebar{left:487px;top:252px;width:187px;height:824px;background:var(--panel)}
.search{left:493px;top:213px;width:152px;height:20px;border-radius:10px;background:#dcdcdc;font-family:"Ubuntu",sans-serif;font-weight:500;font-size:9px;color:#666;padding:5px 10px}
.search-icon{left:650px;top:211px}
.members{left:630px;top:245px;width:52px;height:53px;background:var(--white);border:1px solid #ddd;text-align:center}
.members b{display:block;font-family:"Ubuntu",sans-serif;font-weight:500;font-size:22px;padding-top:6px;border-bottom:1px solid #e5e5e5;height:35px}
.members small{font-size:7.5px;color:#555;line-height:16px}
.side-h{font-family:"Arimo",sans-serif;font-weight:700;font-size:13px}
.side-p{font-size:10.6px;line-height:17.4px;color:#222;width:165px}
.side-p.small{font-size:9.8px;line-height:15.5px;color:#555}
.user{left:501px;width:159px;height:49px;background:var(--white);border:1px solid #ddd}
.user .pic{position:absolute;left:9px;top:8px;width:31px;height:31px}
.user .name{position:absolute;left:47px;top:10px;font-family:"Arimo",sans-serif;font-weight:700;font-size:10px;color:var(--orange)}
.user .role{position:absolute;left:47px;top:28px;font-size:8.5px;color:#444}
.user .num{position:absolute;right:12px;top:28px;font-size:8.5px;font-weight:700;color:#444}
.tagbar{left:501px;height:14px;background:var(--white);border:1px solid #ddd;font-size:7.5px;font-weight:700;color:#999;padding:0 4px;line-height:12px;display:flex;justify-content:space-between}
.footer-links{left:496px;top:1088px;font-size:7.5px;color:var(--orange)}
.footer-links span{color:#ccc;margin:0 3px}

.licence{left:247px;top:1152px;height:18px;background:rgba(40,40,40,.75);color:var(--white);font-size:8.5px;line-height:18px;padding:0 6px;border-radius:2px}
.licence i{display:inline-block;width:55px;height:8px;background:#ddd;margin-right:4px;vertical-align:-1px}
.licence a{color:var(--orange)}
.hubbox{left:734px;top:1140px;width:161px;height:41px;border:1px solid #999;background:rgba(40,40,40,.6);color:var(--white)}
.hubbox .name{position:absolute;left:10px;top:8px;font-family:"Ubuntu",sans-serif;font-weight:700;font-size:19px}
.hubbox .sep{position:absolute;left:82px;top:7px;height:26px;border-left:1px solid #999}
.hubbox .cta{position:absolute;left:93px;top:9px;font-size:8.5px;line-height:12px}
</style>
</head>
<body>

<div class="abs page">
  <header class="abs header">
    <div class="abs tape" style="left:10px;top:170px;width:120px;height:30px;transform:rotate(4deg)"></div>
    <div class="abs tape" style="left:250px;top:172px;width:120px;height:26px"></div>
    <div class="abs header-art" role="img" aria-label="Piglet, black piglet, puppy and dachshund peeking in a row"></div>
    <div class="abs logo">critterask</div>
    <div class="abs logo-dot"></div>
    <div class="abs tagline">the best website for our best friends</div>
    <div class="abs join"><a href="#">Join</a><small>or</small></div>
    <a class="abs btn-ask-top" href="#">Ask a question</a>
    <nav class="abs nav"><a href="#">Home</a><a href="#">Help</a><a href="#">Sign in</a><a href="#">Sign up</a></nav>
  </header>

  <h1 class="abs h-ask">Ask a Question</h1>
  <div class="abs avatar" style="left:25px;top:254px">
    <svg width="32" height="32" viewBox="0 0 32 32"><circle cx="16" cy="12" r="6" fill="#fff"/><path d="M4 32c0-8 5-12 12-12s12 4 12 12z" fill="#fff"/></svg>
  </div>
  <div class="abs composer"></div>
  <div class="abs tag-input">Tag this question</div>
  <div class="abs btn-ask">Ask Question</div>
  <div class="abs dash" style="top:395px"></div>

  <h2 class="abs h-latest">Latest Questions</h2>
  <div class="abs rss"></div>
  <div class="abs tabs">
    <div class="tab active" style="left:0;width:58px">Questions</div>
    <div class="tab" style="left:61px;width:72px">Popular</div>
    <div class="tab" style="left:136px;width:48px">Activity</div>
  </div>

  <ul class="abs questions">
    <li class="q four"><div class="avatar"><svg width="32" height="32" viewBox="0 0 32 32"><circle cx="16" cy="12" r="6" fill="#fff"/><path d="M4 32c0-8 5-12 12-12s12 4 12 12z" fill="#fff"/></svg></div><div class="count">0</div>
      <h3>Hello my cat has a sprained leg or so i think its sprained it quivers whene i strech it all the way should i massage it or let it heal this is the second insident he seems so desprate and sleeps all day. Please help?</h3>
      <p class="meta">Asked by <a href="#">oriel</a><span class="tag">my cat is in pain and depressed</span></p></li>
    <li class="q"><div class="avatar photo" role="img" aria-label="Member photo"></div><div class="count">0</div>
      <h3>My dog is small but has a huge weeny is that Normal?</h3>
      <p class="meta">Asked by <a href="#">Briarfox</a><span class="tag">yorkie</span></p></li>
    <li class="q"><div class="avatar photo" role="img" aria-label="Member photo"></div><div class="count">1</div>
      <h3>Can I clean my dog's ear with hydrogen peroxide?</h3>
      <p class="meta">Asked by <a href="#">Dovan</a><span class="tag">ear</span></p></li>
    <li class="q two"><div class="avatar photo" role="img" aria-label="Member photo"></div><div class="count">1</div>
      <h3>My dog is scratching her ear and shaking her head. What is wrong?</h3>
      <p class="meta">Asked by <a href="#">Dovan</a><span class="tag">ear</span></p></li>
    <li class="q"><div class="avatar"><svg width="32" height="32" viewBox="0 0 32 32"><circle cx="16" cy="12" r="6" fill="#fff"/><path d="M4 32c0-8 5-12 12-12s12 4 12 12z" fill="#fff"/></svg></div><div class="count">1</div>
      <h3>What do I do for an infected wound on my dog's leg?</h3>
      <p class="meta">Asked by <a href="#">Pawsmom</a><span class="tag">injury</span></p></li>
    <li class="q"><div class="avatar"><svg width="32" height="32" viewBox="0 0 32 32"><circle cx="16" cy="12" r="6" fill="#fff"/><path d="M4 32c0-8 5-12 12-12s12 4 12 12z" fill="#fff"/></svg></div><div class="count">2</div>
      <h3>How do I keep my dog from licking a wound on his leg?</h3>
      <p class="meta">Asked by <a href="#">Pawsmom</a><span class="tag">grooming</span></p></li>
    <li class="q two"><div class="avatar"><svg width="32" height="32" viewBox="0 0 32 32"><circle cx="16" cy="12" r="6" fill="#fff"/><path d="M4 32c0-8 5-12 12-12s12 4 12 12z" fill="#fff"/></svg></div><div class="count">1</div>
      <h3>My dog has a broken toe nail, what do i do? She is licking it a lot and won't let me touch her foot.</h3>
      <p class="meta">Asked by <a href="#">Pawsmom</a><span class="tag">grooming</span></p></li>
    <li class="q"><div class="avatar"><svg width="32" height="32" viewBox="0 0 32 32"><circle cx="16" cy="12" r="6" fill="#fff"/><path d="M4 32c0-8 5-12 12-12s12 4 12 12z" fill="#fff"/></svg></div><div class="count">1</div>
      <h3>Can little dogs get arthritis?</h3>
      <p class="meta">Asked by <a href="#">Wendeline</a><span class="tag">arthritis</span></p></li>
    <li class="q"><div class="avatar"><svg width="32" height="32" viewBox="0 0 32 32"><circle cx="16" cy="12" r="6" fill="#fff"/><path d="M4 32c0-8 5-12 12-12s12 4 12 12z" fill="#fff"/></svg></div><div class="count">1</div>
      <h3>How do I know if my dog has arthritis?</h3>
      <p class="meta">Asked by <a href="#">Wendeline</a><span class="tag">arthritis</span></p></li>
    <li class="q"><div class="avatar"><svg width="32" height="32" viewBox="0 0 32 32"><circle cx="16" cy="12" r="6" fill="#fff"/><path d="M4 32c0-8 5-12 12-12s12 4 12 12z" fill="#fff"/></svg></div><div class="count">1</div>
      <h3>My dog seems sore can I give him Ibuprofen?</h3>
      <p class="meta">Asked by <a href="#">Wendeline</a><span class="tag">pain</span></p></li>
  </ul>

  <div class="abs pager">
    <span class="current">1</span><span>2</span><span>3</span><span>4</span><span>5</span><span>6</span><span>7</span><span>…</span><span>243</span><span>244</span><span>245</span><span>Next</span>
  </div>

  <aside class="abs sidebar"></aside>
  <div class="abs search">Search...</div>
  <svg class="abs search-icon" width="22" height="22" viewBox="0 0 22 22"><circle cx="9" cy="9" r="6.5" fill="none" stroke="#c8c8c8" stroke-width="3"/><path d="M14 14l6 6" stroke="#c8c8c8" stroke-width="3.5" stroke-linecap="round"/></svg>
  <div class="abs members"><b>277</b><small>Members</small></div>

  <h3 class="abs side-h" style="left:501px;top:295px">Welcome</h3>
  <p class="abs side-p" style="left:501px;top:318px">CritterAsk.net is Q&amp;A community dedicated to helping pet owners all over the world.</p>
  <p class="abs side-p small" style="left:501px;top:378px">Got a problem pooch or trouble with a tortoise? Get free answers from the CritterAsk.net community.</p>

  <h3 class="abs side-h" style="left:501px;top:469px">Most active</h3>
  <div class="abs user" style="top:492px"><div class="pic" role="img" aria-label="Member photo" style="background:linear-gradient(#7b8aa0,#3a3f48)"></div><span class="name">Mara Lindqvist, DVM</span><span class="role">Answers</span><span class="num">43</span></div>
  <div class="abs user" style="top:549px"><div class="pic" role="img" aria-label="Member photo" style="background:linear-gradient(#9fb56a,#c9a46a)"></div><span class="name">Juniper</span><span class="role">Answers</span><span class="num">37</span></div>
  <div class="abs user" style="top:605px"><div class="pic" role="img" aria-label="Member photo" style="background:linear-gradient(#8794a8,#2d2f35)"></div><span class="name">Tamsin</span><span class="role">Answers</span><span class="num">33</span></div>

  <h3 class="abs side-h" style="left:501px;top:685px">Popular tags</h3>
  <div class="abs tagbar" style="top:706px;width:155px"><span>health concerns</span><span>238</span></div>
  <div class="abs tagbar" style="top:726px;width:144px"><span>weight</span><span>237</span></div>
  <div class="abs tagbar" style="top:746px;width:133px"><span>life expectancy</span><span>236</span></div>
  <div class="abs tagbar" style="top:766px;width:122px"><span>colors</span><span>236</span></div>
  <div class="abs tagbar" style="top:786px;width:111px"><span>temperament</span><span>236</span></div>

  <div class="abs footer-links">Terms<span>|</span>Disclaimer<span>|</span>Privacy<span>|</span>Contact<span>|</span>Report</div>
</div>

<div class="abs licence"><i></i>This work is licenced under a <a href="#">Open Share Licence</a></div>
<div class="abs hubbox"><span class="name">Zorvat</span><span class="sep"></span><span class="cta">Create your<br>own Zorvat</span></div>

</body>
</html>
```